Medical Skincare services/menu/pricing Booklet 12 pages

We need produce a 12-page glossy, saddle-stitched booklet (5 1/2" tall X 81/2" wide). The booklet will be used as a services menu for a skin care salon. I have mocked up the booklet (w/ all copy) in WORD and I've provided a separate PDF of the accurate page order (see files attached). IMPORTANT: Feel free to use your creativity yet style-wise it should kinda match my wife's website colors and text style. Her clients are demanding so she wants a clean, high end, modern look (ala Apple maybe?). See her website for a frame of reference www.GlowWithMara.com
Updates

Target Market(s)

upscale female, professional women, teens with acne

Industry/Entity Type

Medical

Requirements
Must have
• the pics in the mock up are important. I've attached them here

```html
<!DOCTYPE html>
<html lang="en">
<head>
<meta charset="utf-8">
<title>Glow With Mara – Services Booklet Spreads</title>
<link rel="stylesheet" href="https://fonts.googleapis.com/css2?family=Oswald:wght@400;500;600;700&family=Open+Sans:wght@400;600;700&family=Cormorant+Garamond:wght@500&display=swap">
<style>
:root{
  --bg-top:#ffffff;
  --bg-bottom:#cfcfcf;
  --ink:#1a1a1a;
  --black:#0d0d0d;
  --blush:#fbefe8;
  --blush-deep:#f6e3d8;
  --silver:#c4c4c4;
  --mist:#dfe7ef;
  --grey-text:#8d969f;
  --white:#ffffff;
}
*{box-sizing:border-box;margin:0;padding:0}
html,body{width:1200px;height:1200px;overflow:hidden}
body{background:linear-gradient(var(--bg-top),var(--bg-bottom));position:relative;font-family:"Open Sans",Arial,sans-serif;color:var(--ink)}
.page{position:absolute;overflow:hidden;background:var(--white);box-shadow:0 4px 10px rgba(0,0,0,.35)}
.heading{font-family:"Oswald",Arial,sans-serif;font-weight:400;text-transform:uppercase}
.photo{position:absolute}

/* cover */
.cover{left:26px;top:28px;width:560px;height:367px;background:var(--black)}
.cover .wordmark{position:absolute;left:22px;top:108px;font-family:"Oswald",sans-serif;font-weight:600;color:var(--silver);line-height:.9}
.cover .wordmark .big{display:block;font-size:104px;letter-spacing:2px}
.cover .wordmark .small{display:block;font-size:22px;letter-spacing:9px;margin-top:6px}
.cover .menu{position:absolute;left:402px;top:116px;list-style:none;color:#e8e8e8;font-size:10.5px;line-height:16px}
.cover .menu li::before{content:"";display:inline-block;width:4px;height:4px;border-radius:50%;background:#e8e8e8;margin:0 9px 2px 0}
.cover .footer{position:absolute;left:0;bottom:0;width:100%;height:33px;background:var(--blush);text-align:center;line-height:33px;font-size:10.5px;letter-spacing:3.2px;color:#333}

/* about */
.about{left:618px;top:28px;width:559px;height:367px;background:var(--blush)}
.about .copy{position:absolute;left:38px;top:24px;width:186px}
.about h2{font-size:18px;line-height:23px;color:#222;margin-bottom:10px;white-space:nowrap}
.about p{font-size:6.4px;line-height:8.5px;text-align:justify;color:#333;margin-bottom:14px}
.about .photo{right:0;top:0;width:279px;height:367px;background:linear-gradient(160deg,#cfc7ba,#8d9a97 55%,#3f5c63)}

/* testimonials */
.reviews{left:24px;top:417px;width:560px;height:365px}
.reviews .band{height:50px;background:linear-gradient(90deg,#b4b4b4,#f2f2f2 50%,#b4b4b4);text-align:center;border-bottom:2px solid #333}
.reviews .band h2{font-family:"Oswald",sans-serif;font-weight:700;font-size:18px;line-height:50px;letter-spacing:.3px}
.quote{position:absolute;font-size:7.2px;line-height:9.6px;color:#333}
.quote p{padding-left:10px;position:relative}
.quote p::before{content:"";position:absolute;left:0;top:3px;width:4px;height:4px;border-radius:50%;background:#222}
.quote .by{font-family:"Oswald",sans-serif;font-size:11px;margin-top:4px;color:#222}
.quote .by::before{content:"\201C";display:block;font-size:22px;line-height:16px;color:#aaa;font-family:Georgia,serif}
.quote .by small{font-size:8.5px}

/* facial menu */
.facial{left:618px;top:417px;width:559px;height:365px}
.facial .model{left:64px;top:0;width:154px;height:148px;background:radial-gradient(circle at 55% 45%,#f1d7c4,#e7c5ae 55%,#fff 80%)}
.facial .device{left:420px;top:14px;width:78px;height:120px;border-radius:6px;background:linear-gradient(#dfe7f1,#8ea6c4)}
.facial .brand{position:absolute;left:160px;top:84px;font-family:"Oswald",sans-serif;font-weight:400;font-size:30px;color:#333;letter-spacing:.5px}
.facial .tag{position:absolute;left:297px;top:122px;font-size:8px;color:#333}
.facial .rule{position:absolute;left:0;top:147px;width:100%;height:2px;background:#222}
.facial .list{position:absolute;left:30px;top:178px;width:499px;text-align:center}
.facial .list h3{font-family:"Oswald",sans-serif;font-weight:600;font-size:9.5px;margin-top:11px}
.facial .list h3:first-child{margin-top:0}
.facial .list p{font-size:7.2px;line-height:9.6px;color:#333}
.facial .base{position:absolute;left:0;bottom:0;width:100%;height:14px;background:var(--black)}

/* laser */
.laser{left:24px;top:806px;width:560px;height:366px}
.laser .hero{left:0;top:0;width:560px;height:166px;background:linear-gradient(90deg,#e9dcd2 0,#dfe7ef 40%,#edf1f5)}
.laser .ghost{position:absolute;left:194px;top:40px;font-family:"Oswald",sans-serif;font-weight:400;color:var(--grey-text);line-height:.9}
.laser .ghost span{display:block;font-size:50px;letter-spacing:2px}
.laser .ghost span+span{font-size:34px;margin-left:74px;margin-top:-8px;opacity:.75}
.laser .caption{position:absolute;left:40px;top:150px;font-family:"Cormorant Garamond",serif;font-size:12.5px;color:#444;letter-spacing:.3px;text-transform:uppercase}
.laser .rule{position:absolute;left:0;top:166px;width:100%;height:2px;background:#222}
.laser h2{position:absolute;left:0;top:174px;width:100%;text-align:center;font-family:"Oswald",sans-serif;font-weight:700;font-size:26px}
.laser .sub{position:absolute;left:0;top:206px;width:100%;text-align:center;font-family:"Oswald",sans-serif;font-size:14px}
.laser .note{position:absolute;left:40px;top:228px;width:480px;text-align:center;font-size:7.2px;line-height:9.6px}
.laser .prices{position:absolute;left:0;top:258px;width:100%;height:108px;background:var(--blush-deep)}
.laser .price{position:absolute;top:6px;font-family:"Oswald",sans-serif;font-size:8.5px}
.laser .price b{font-size:11px;font-weight:700}
.laser .circle{position:absolute;top:21px;width:79px;height:79px;border-radius:50%;border:3px solid #f3d9c8}

/* contact */
.contact{left:619px;top:806px;width:558px;height:366px;background:var(--black);color:var(--white)}
.contact .photo{right:0;top:0;width:226px;height:366px;background:linear-gradient(160deg,#6b5547,#3b3331 50%,#8f8f8f)}
.contact .info{position:absolute;left:15px;top:12px}
.contact h2{font-size:17px;font-weight:400;margin:0 0 5px}
.contact .row{display:flex;gap:7px;font-size:10.5px;font-weight:600;line-height:14.5px;margin-bottom:12px}
.contact .row svg{flex:none;margin-top:3px}
.contact .wordmark{position:absolute;left:15px;top:305px;font-family:"Oswald",sans-serif;font-weight:600;color:var(--silver);font-size:30px;letter-spacing:1px}
</style>
</head>
<body>

<section class="page cover">
  <div class="wordmark"><span class="big">GLOW</span><span class="small">WITH MARA</span></div>
  <ul class="menu">
    <li>AquaPure Facial</li><li>LumaGenesis</li><li>PL (Brightline)</li><li>Vascular</li>
    <li>Microneedling Pro</li><li>LED Light Therapy</li><li>Vita Peel</li>
    <li>Customized Facials &amp; Peels</li><li>Dermaplane</li>
  </ul>
  <div class="footer">www.GlowWithMara.com</div>
</section>

<section class="page about">
  <div class="copy">
    <h2 class="heading">Mara Whitfield Medical<br>Aesthetician &amp; Owner</h2>
    <p>As a teenager, I had cystic acne so bad that I would ditch school to swim in the ocean because the salt water seemed to dry out and heal my skin. I was on such a mission to clear my skin that I spent my weekly allowance on skin care products I saw on TV. Then, I memorized every ingredient. I was so intrigued by the beauty industry that, by 19, I began a career as a make up artist for Maison Lune, Veyra, Corin Blake, Solstice and Avenly. By 23, I was a skincare consultant for the Celeste Marlow Salons in Beverly Hills and Orange County California. I was honored to learn from the world's most demanding clients.</p>
    <h2 class="heading">I understand why<br>your skin matters</h2>
    <p>Admit it. We take more pictures of ourselves than ever…and then try to "fix" our blemishes with photo filters. I understand your frustrations. Some of you know I've had a parallel career as a professional singer with dozens of network TV appearances; where the HD cameras take extreme close ups…Yikes!). I also sing the National Anthem at pro football, basketball and baseball games, where their 200 foot-wide screens constantly remind me that skin imperfections are magnified. I will help get your skin more naturally beautiful so you can use less photo filters ;-)</p>
  </div>
  <div class="photo" role="img" aria-label="Portrait of the owner in a long patterned dress standing beside a flower planter"></div>
</section>

<section class="page reviews">
  <div class="band"><h2>TESTIMONIALS</h2></div>
  <div class="quote" style="left:28px;top:70px;width:250px">
    <p>Mara is someone I definitely trust with my skincare needs because she truly cares about people and their issues.</p>
    <div class="by" style="margin-left:68px">TESSA ROWLAND<br><small>Reality TV Star/Coastal Lives</small></div>
  </div>
  <div class="quote" style="left:296px;top:70px;width:246px">
    <p>I have been seeing Mara Whitfield for AquaPure Facials. Ever since my first facial my skin has had a healthy glow and texture. As an Aesthetic Professional, she helps me feel my personal best.</p>
    <div class="by" style="margin-left:130px">DANA PERRIN, <small>R.N.</small></div>
  </div>
  <div class="quote" style="left:29px;top:178px;width:250px">
    <p>Having ethnic skin I've been hesitant about having treatments but Mara immediately put me at ease. She has taught me so much about my skin and how to care for it. Each time I've left with my skin looking and feeling amazing.</p>
    <div class="by" style="margin-left:78px">LENA ORTIZ - <small>Real Estate Agent</small></div>
  </div>
  <div class="quote" style="left:287px;top:178px;width:250px">
    <p>I have now had two facials by Mara and each time my skin feels so refreshed and new! She has also helped my teenage son who has acne. Mara knew exactly what he needed and is already getting clearer skin. Worth every penny.</p>
    <div class="by" style="margin-left:75px">KIRA HOLT - <small>Mother of Five</small></div>
  </div>
  <div class="quote" style="left:34px;top:288px;width:490px">
    <p>I've been seeing Mara on a regular basis because she always goes above and beyond to ensure that I'm comfortable. She made the experience all about me and my skincare needs. She is highly knowledgeable and offers creative options to make sure I get what I need.</p>
    <div class="by" style="margin-left:340px">ERIN VASKO - <small>Marketing Exec.</small></div>
  </div>
</section>

<section class="page facial">
  <div class="photo model" role="img" aria-label="Smiling woman with treatment lines on her cheek"></div>
  <div class="photo device" role="img" aria-label="Facial treatment machine on a wheeled stand"></div>
  <div class="brand">AquaPure Facial</div>
  <div class="tag">Radiance Every Day</div>
  <div class="rule"></div>
  <div class="list">
    <h3>AQUAPURE FACIAL is for…</h3>
    <p>Fine Lines and Wrinkles - Elasticity and Firmness - Even Skin Tone and Vibrancy - Oil and Congested skin - Enlarged Pores - Brown Spots</p>
    <h3 style="margin-top:16px">SIGNATURE AQUAPURE $149 (30 MIN)</h3>
    <p>Deep cleanse and exfoliation, extracts, and hydrates your skin utilizing super serums filled with antioxidants, peptides and hyaluronic acid</p>
    <h3 style="margin-top:16px">AGE-REFINEMENT AQUAPURE $175</h3>
    <p>Includes PeptiBoost to reduce the appearance of fine lines and wrinkles. Plumps your skin to a youthful state.</p>
    <h3 style="margin-top:16px">PLATINUM AQUAPURE $250</h3>
    <p>The ultimate AquaPure Experience! Begin the detoxification process with Lymphatic Drainage. Then, the signature facial deeply cleanses, exfoliates, extracts and hydrates the skin while addressing your specific skin concern with a Booster of your choice. Treatment concludes with LED Light Therapy to reduce signs of aging.</p>
  </div>
  <div class="base"></div>
</section>

<section class="page laser">
  <div class="photo hero" role="img" aria-label="Smiling mature woman touching her cheek against a soft blue backdrop"></div>
  <div class="ghost"><span>LUMA</span><span>GENESIS</span></div>
  <div class="caption">Treatment of wrinkles, large pores, skin texture &amp; redness</div>
  <div class="rule"></div>
  <h2>LUMAGENESIS</h2>
  <div class="sub">VASCULAR/Broken Capillaries</div>
  <p class="note">This is a non-ablative procedure that improves skin textures, redness/rosacea, enlarged pores, and scars w/ NO DOWNTIME.<br>(recommended every two weeks)</p>
  <div class="prices">
    <div class="price" style="left:114px">Individual Treatment <b>$250</b></div>
    <div class="price" style="left:345px">Series Package of (6) <b>$1,275</b></div>
    <div class="circle" role="img" aria-label="Before treatment skin close-up" style="left:74px;background:radial-gradient(#c78c7c,#6d4a3e)"></div>
    <div class="circle" role="img" aria-label="After treatment skin close-up" style="left:171px;background:radial-gradient(#b98a76,#5a3f35)"></div>
    <div class="circle" role="img" aria-label="Before treatment cheek close-up" style="left:306px;background:radial-gradient(#d98b86,#7a3e3a)"></div>
    <div class="circle" role="img" aria-label="After treatment cheek close-up" style="left:403px;background:radial-gradient(#d9a08f,#6e4338)"></div>
  </div>
</section>

<section class="page contact">
  <div class="photo" role="img" aria-label="Portrait of the owner in a grey knit sweater with a fur collar"></div>
  <div class="info">
    <h2 class="heading">Book Online</h2>
    <div class="row" style="margin-bottom:2px"><svg width="9" height="8" viewBox="0 0 9 8"><rect width="9" height="6" rx="1" fill="#fff"/><path d="M2 6v2l2-2z" fill="#fff"/></svg><span>(555) 014-2277</span></div>
    <div class="row"><svg width="9" height="9" viewBox="0 0 10 10"><circle cx="5" cy="5" r="4.3" fill="none" stroke="#fff"/><path d="M.7 5h8.6M5 .7c-2.5 2.5-2.5 6 0 8.6M5 .7c2.5 2.5 2.5 6 0 8.6" fill="none" stroke="#fff" stroke-width=".8"/></svg><span>www.GlowWithMara.com</span></div>
    <h2 class="heading">Location:</h2>
    <div class="row"><svg width="8" height="11" viewBox="0 0 8 11"><path d="M4 0a4 4 0 0 1 4 4c0 3-4 7-4 7S0 7 0 4a4 4 0 0 1 4-4z" fill="#fff"/><circle cx="4" cy="4" r="1.5" fill="#0d0d0d"/></svg><span>Glow With Mara<br>4120 Aspen Way #200<br>Ridgefield, Colorado 80000</span></div>
    <h2 class="heading">By Appt. Hours:</h2>
    <div class="row"><svg width="10" height="10" viewBox="0 0 10 10"><circle cx="5" cy="5" r="5" fill="#fff"/><path d="M5 2v3h2" fill="none" stroke="#0d0d0d" stroke-width="1.2"/></svg><span>Monday: 10:00-am-4:00pm<br>Tuesday: 10:00pm-6:00pm<br>Wednesday: 10:00am-6:00pm<br>Thursda: 10:00am-6:00pm<br>Friday: 10:00am-6:00pm<br>Saturday: 10:00-4:00pm<br>Sunday: Closed</span></div>
  </div>
  <div class="wordmark">GLOW WITH MARA</div>
</section>

</body>
</html>
```